Veterinary Pylon

My veterinary clinic is not clearly visible from the street and I want to place a Pylon next to my driveway. I want a modern, elegant straight Design, the Photo shows the sheduled place. One can see the clinic on our Homepage: www.tailbright-vethaus.at
The last pictures are examples for pylones I like

Target Market(s)

the passing cars often miss my entry...I want to show where to turn left

Colors
3276b5
33a6d7
00a990

Requirements
Must have
• High value, simple elegance, size: 250cm (high) x 100cm (width)
Nice to have
• Our Logo, arrow(?)

A special Text is not necessary but this will be an option:

Biegen sie hier ab und wir biegen es wieder hin!
Should not have
• Too much Color, the colors I have chosen are the possible colors but it‘s not necessary to use them.

```html
<!DOCTYPE html>
<html lang="de">
<head>
<meta charset="utf-8">
<title>Tailbright Vethaus – Pylon</title>
<link rel="stylesheet" href="https://fonts.googleapis.com/css2?family=Michroma&display=swap">
<style>
  :root {
    --navy: #124c94;
    --sky: #2ebbdf;
    --white: #ffffff;
  }
  html, body {
    margin: 0;
    padding: 0;
    width: 1200px;
    height: 3000px;
    overflow: hidden;
    background: var(--white);
  }
  .pylon {
    position: relative;
    width: 1200px;
    height: 3000px;
    background: var(--white);
    overflow: hidden;
  }
  .pylon__waves {
    position: absolute;
    inset: 0;
    width: 1200px;
    height: 3000px;
  }
  .brand-dot {
    position: absolute;
    left: 450px;
    top: 540px;
    width: 300px;
    height: 300px;
    border-radius: 50%;
    background: var(--sky);
  }
  .brand-name {
    position: absolute;
    left: 0;
    top: 1010px;
    width: 1200px;
    margin: 0;
    text-align: center;
    font-family: "Michroma", sans-serif;
    font-weight: 400;
    color: var(--navy);
    line-height: 1.15;
  }
  .brand-name__main {
    display: block;
    font-size: 112px;
    letter-spacing: 2px;
  }
  .brand-name__sub {
    display: block;
    font-size: 58px;
    letter-spacing: 22px;
    margin-top: 30px;
  }
</style>
</head>
<body>
<main class="pylon">
  <svg class="pylon__waves" viewBox="0 0 1200 3000" xmlns="http://www.w3.org/2000/svg" aria-hidden="true">
    <defs>
      <linearGradient id="arrow-fade" gradientUnits="userSpaceOnUse" x1="400" y1="0" x2="838" y2="0">
        <stop offset="0" stop-color="#124c94"/>
        <stop offset="1" stop-color="#2ebbdf"/>
      </linearGradient>
    </defs>
    <!-- top band -->
    <path class="wave-light" fill="var(--sky)" d="M560 0 H1200 V398 C1010 378 830 320 680 222 C620 180 590 100 560 0 Z"/>
    <path class="wave-dark" fill="var(--navy)" d="M0 0 H1200 V48 C960 180 720 240 500 235 C330 232 160 200 0 140 Z"/>
    <!-- direction arrow -->
    <g class="turn-arrow" fill="none" stroke="url(#arrow-fade)" stroke-width="38" stroke-linejoin="miter" stroke-miterlimit="10">
      <path d="M570 1496 L415 1651 L570 1806"/>
      <path d="M425 1651 H838"/>
    </g>
    <!-- bottom band -->
    <path class="wave-light" fill="var(--sky)" d="M0 1955 C180 1950 330 1985 470 2050 L0 2320 Z"/>
    <path class="wave-dark" fill="var(--navy)" d="M0 2262 C250 2090 520 2005 800 2004 C950 2004 1080 2030 1200 2068 V3000 H0 Z"/>
  </svg>

  <div class="brand-dot" aria-hidden="true"></div>
  <h1 class="brand-name">
    <span class="brand-name__main">TAILBRIGHT</span>
    <span class="brand-name__sub">VETHAUS</span>
  </h1>
</main>
</body>
</html>
```